I have an animal hospital. I want a poster to hang in each exam room to show a picture of a normal sized heart and then an enlarged heart of a dog that was fed a grain-free diet. I want to warn people not to feed grain-free diets. Maybe at the top of the poster, "Do you feed grain-free?" and then the x-ray comparison, then the warnings of Canine Dilated Cardiomyopathy.

```html
<!DOCTYPE html>
<html lang="en">
<head>
<meta charset="utf-8">
<title>Do You Feed Grain-Free? – Exam Room Poster</title>
<link href="https://fonts.googleapis.com/css2?family=Luckiest+Guy&family=Poppins:wght@500;600;700&display=swap" rel="stylesheet">
<style>
  :root{
    --page-bg:#e4e4e4;
    --sky-top:#8fd0f0;
    --sky-mid:#ade0f7;
    --sky-low:#9fd7f3;
    --ink:#0b1a22;
    --navy:#123d5c;
    --accent:#1f6fa8;
    --panel:#5eb1e0;
    --panel-strip:#4aa3d8;
    --outline-blue:#3f93cf;
    --plus:#6fb9e4;
    --heart-deep:#c0404a;
    --heart-light:#ee9a8c;
    --xray-dark:#1a1a1a;
    --xray-light:#bdbdbd;
    --warn-yellow:#ffd21f;
    --coat-light:#eee3cf;
    --coat-tan:#d8bf98;
    --coat-brown:#8a5e45;
  }
  *{margin:0;padding:0;box-sizing:border-box}
  html,body{width:1200px;height:2588px;overflow:hidden;background:var(--page-bg)}
  .poster{
    position:absolute;left:88px;top:526px;width:1024px;height:1536px;overflow:hidden;
    background:linear-gradient(180deg,var(--sky-top) 0%,var(--sky-mid) 45%,var(--sky-low) 100%);
    font-family:"Poppins",sans-serif;color:var(--navy);
    box-shadow:0 6px 18px rgba(0,0,0,.18);
  }
  .plus{position:absolute;fill:var(--plus);opacity:.7}
  .kicker{
    position:absolute;left:0;right:0;top:52px;text-align:center;
    font-family:"Luckiest Guy",sans-serif;font-size:62px;line-height:70px;letter-spacing:2px;
    color:#eaf7fd;-webkit-text-stroke:3px var(--outline-blue);
  }
  .headline{
    position:absolute;left:0;right:0;top:124px;text-align:center;
    font-family:"Luckiest Guy",sans-serif;font-size:118px;line-height:124px;letter-spacing:3px;color:var(--ink);font-weight:400;
  }
  .heart{position:absolute;border-radius:28px;
    background:radial-gradient(ellipse at 55% 58%,var(--heart-deep) 0%,#d45f5c 50%,var(--heart-light) 85%,rgba(238,154,140,0) 100%);}
  .heart--normal{left:140px;top:335px;width:230px;height:240px}
  .heart--enlarged{left:575px;top:272px;width:310px;height:303px}
  .heart-shadow{position:absolute;height:4px;border-radius:50%;background:rgba(0,0,0,.45)}
  .diet-label{
    position:absolute;top:596px;height:30px;border:2px solid var(--navy);border-radius:8px;
    font-size:19px;font-weight:600;line-height:27px;color:var(--navy);text-align:center;white-space:nowrap;
  }
  .xray-panel{position:absolute;left:0;top:670px;width:458px;height:490px;background:var(--panel);border-radius:0 30px 30px 0}
  .xray-strip{position:absolute;right:0;top:0;width:67px;height:100%;background:var(--panel-strip);border-radius:0 30px 30px 0}
  .xray-title{
    position:absolute;left:33px;top:50%;transform:translate(-50%,-50%) rotate(90deg);white-space:nowrap;
    color:#fff;font-weight:700;font-size:29px;letter-spacing:.5px;
  }
  .xray{position:absolute;left:61px;width:312px;height:193px;border:2px solid #fff;border-radius:10px;
    background:radial-gradient(ellipse at 40% 50%,var(--xray-light) 0%,#777 35%,var(--xray-dark) 80%)}
  .xray--one{top:37px}
  .xray--two{top:260px}
  .warn-icon{position:absolute;left:496px;top:672px;width:60px;height:54px}
  .warn-title{position:absolute;left:575px;top:664px;font-size:28px;font-weight:700;line-height:34px;color:var(--navy);white-space:nowrap}
  .warn-title span{color:var(--accent)}
  .bracket{position:absolute;left:670px;top:702px;width:290px;height:492px}
  .symptoms{position:absolute;left:505px;top:757px;width:390px;list-style:none}
  .symptoms li{position:relative;padding-left:51px;font-size:21.5px;font-weight:500;line-height:26px;color:var(--navy)}
  .symptoms li svg{position:absolute;left:0;top:0;width:28px;height:26px}
  .dogs{position:absolute;left:0;right:0;bottom:0;height:320px;
    border:4px solid var(--outline-blue);border-bottom:0;border-radius:60px 60px 0 0;
    background:linear-gradient(90deg,var(--coat-tan) 0%,var(--coat-light) 25%,var(--coat-brown) 42%,var(--coat-light) 58%,var(--coat-tan) 78%,var(--coat-light) 100%)}
</style>
</head>
<body>
<main class="poster">
  <svg class="plus" style="left:140px;top:10px" width="40" height="40" viewBox="0 0 3 3"><path d="M1 0h1v1h1v1H2v1H1V2H0V1h1z"/></svg>
  <svg class="plus" style="left:18px;top:75px" width="80" height="80" viewBox="0 0 3 3"><path d="M1 0h1v1h1v1H2v1H1V2H0V1h1z"/></svg>
  <svg class="plus" style="left:0;top:225px" width="30" height="30" viewBox="0 0 3 3"><path d="M1 0h1v1h1v1H2v1H1V2H0V1h1z"/></svg>
  <svg class="plus" style="left:960px;top:1075px" width="60" height="60" viewBox="0 0 3 3"><path d="M1 0h1v1h1v1H2v1H1V2H0V1h1z"/></svg>
  <svg class="plus" style="left:795px;top:1060px" width="50" height="50" viewBox="0 0 3 3"><path d="M1 0h1v1h1v1H2v1H1V2H0V1h1z"/></svg>

  <div class="kicker">DO YOU FEED</div>
  <h1 class="headline">GRAIN-FREE?</h1>

  <div class="heart heart--normal" role="img" aria-label="Illustration of a normal sized dog heart, cross-section"></div>
  <div class="heart-shadow" style="left:160px;top:577px;width:225px"></div>
  <div class="heart heart--enlarged" role="img" aria-label="Illustration of an enlarged dog heart, cross-section"></div>
  <div class="heart-shadow" style="left:588px;top:577px;width:300px"></div>

  <div class="diet-label" style="left:163px;width:196px">WITH GRAIN DIET</div>
  <div class="diet-label" style="left:648px;width:196px">GRAIN FREE DIET</div>

  <section class="xray-panel">
    <div class="xray xray--one" role="img" aria-label="Chest X-ray of a dog with a normal heart"></div>
    <div class="xray xray--two" role="img" aria-label="Chest X-ray of a dog with an enlarged heart"></div>
    <div class="xray-strip"><div class="xray-title">X-RAY COMPARISON</div></div>
  </section>

  <svg class="warn-icon" viewBox="0 0 60 54"><path d="M30 3 57 51H3z" fill="var(--warn-yellow)" stroke="#111" stroke-width="3.5" stroke-linejoin="round"/><rect x="27.5" y="17" width="5" height="21" rx="2" fill="#111"/><circle cx="30" cy="44" r="3" fill="#111"/></svg>
  <h2 class="warn-title">The warnings of <span>Canine</span><br><span>Dilated Cardiomyopathy</span></h2>

  <svg class="bracket" viewBox="0 0 290 492" fill="none"><path d="M270 2h15v481H5" stroke="var(--navy)" stroke-width="3"/><circle cx="5" cy="483" r="7" fill="var(--navy)"/></svg>

  <ul class="symptoms">
    <li style="margin-bottom:24px"><svg viewBox="0 0 28 26"><g fill="var(--ink)"><ellipse cx="14" cy="18" rx="7" ry="6"/><ellipse cx="5" cy="10" rx="3" ry="4"/><ellipse cx="11" cy="5" rx="3" ry="4"/><ellipse cx="18" cy="5" rx="3" ry="4"/><ellipse cx="24" cy="10" rx="3" ry="4"/></g></svg>Rapid breathing when resting or sleeping (more than 30-35 breaths per minute).</li>
    <li style="margin-bottom:24px"><svg viewBox="0 0 28 26"><g fill="var(--ink)"><ellipse cx="14" cy="18" rx="7" ry="6"/><ellipse cx="5" cy="10" rx="3" ry="4"/><ellipse cx="11" cy="5" rx="3" ry="4"/><ellipse cx="18" cy="5" rx="3" ry="4"/><ellipse cx="24" cy="10" rx="3" ry="4"/></g></svg>Increased effort associated with breathing.</li>
    <li style="margin-bottom:24px"><svg viewBox="0 0 28 26"><g fill="var(--ink)"><ellipse cx="14" cy="18" rx="7" ry="6"/><ellipse cx="5" cy="10" rx="3" ry="4"/><ellipse cx="11" cy="5" rx="3" ry="4"/><ellipse cx="18" cy="5" rx="3" ry="4"/><ellipse cx="24" cy="10" rx="3" ry="4"/></g></svg>Restless sleeping; moving around a lot and changing positions.</li>
    <li style="margin-bottom:24px"><svg viewBox="0 0 28 26"><g fill="var(--ink)"><ellipse cx="14" cy="18" rx="7" ry="6"/><ellipse cx="5" cy="10" rx="3" ry="4"/><ellipse cx="11" cy="5" rx="3" ry="4"/><ellipse cx="18" cy="5" rx="3" ry="4"/><ellipse cx="24" cy="10" rx="3" ry="4"/></g></svg>Coughing or gagging.</li>
    <li style="margin-bottom:24px"><svg viewBox="0 0 28 26"><g fill="var(--ink)"><ellipse cx="14" cy="18" rx="7" ry="6"/><ellipse cx="5" cy="10" rx="3" ry="4"/><ellipse cx="11" cy="5" rx="3" ry="4"/><ellipse cx="18" cy="5" rx="3" ry="4"/><ellipse cx="24" cy="10" rx="3" ry="4"/></g></svg>Weakness.</li>
    <li><svg viewBox="0 0 28 26"><g fill="var(--ink)"><ellipse cx="14" cy="18" rx="7" ry="6"/><ellipse cx="5" cy="10" rx="3" ry="4"/><ellipse cx="11" cy="5" rx="3" ry="4"/><ellipse cx="18" cy="5" rx="3" ry="4"/><ellipse cx="24" cy="10" rx="3" ry="4"/></g></svg>Reduced ability to exercise.</li>
  </ul>

  <div class="dogs" role="img" aria-label="Photo of a row of puppies and dogs of several breeds"></div>
</main>
</body>
</html>
```